Laser Tattoo Removal Business Cards

We are looking for a professional business card design for a laser tattoo removal business. Ideally looking for a black business card design. The name of the business is Brightline Tattoo Removal. We place our cards at local tattoo shops so we ideally are looking for something trendy/edgy to draw both male and female clientele in.

Target Market(s)

Male/Female ages 18-60

Contact Information for Business Card

black background ideally.. hoping to stay within greys, whites and black

Font styles to use
Serif
Sans Serif

Colors
121212
a9a9a9
5c5c5c
f5f5f5
ffffff
7f7f7f
606060
848484
9d9d9d

Requirements
Must have
• Employee Info:
• Melissa Thornbury
• Chief Executive Offer
• m: 919.537.2846
• w: 919.362.4178
• f: 919.685.3907
• mthornbury@brightlinetattooremoval.example
• Address:
• 4615 Oakmere Pkwy, Suite 210
• Raleigh, NC 27654
• Website:
• www.brightlinetattooremoval.example
Nice to have
• Myabe business name on back or logo on back and employee info on the front

```html
<!DOCTYPE html>
<html lang="en">
<head>
<meta charset="utf-8">
<title>Brightline Tattoo Removal – Business Cards</title>
<link rel="stylesheet" href="https://fonts.googleapis.com/css2?family=Roboto:wght@400;500;700&display=swap">
<style>
  :root {
    --stage: #e6e6e6;
    --card-light: #f5f5f5;
    --card-dark: #121212;
    --ink: #222222;
    --ink-soft: #5c5c5c;
    --ink-muted: #848484;
    --rule: #7f7f7f;
    --white: #ffffff;
  }
  * { box-sizing: border-box; margin: 0; padding: 0; }
  html, body { width: 1200px; height: 960px; overflow: hidden; }
  body {
    position: relative;
    background: var(--stage);
    font-family: "Roboto", Arial, sans-serif;
  }
  .card {
    position: absolute;
    width: 572px;
    height: 342px;
    overflow: hidden;
    box-shadow: 0 2px 6px rgba(0,0,0,0.25);
  }
  .card--front { left: 314px; top: 113px; background: var(--card-light); color: var(--ink); }
  .card--back  { left: 311px; top: 472px; width: 600px; background: var(--card-dark); color: var(--white); }

  .brand-name {
    position: absolute;
    text-align: center;
    font-weight: 500;
    text-transform: uppercase;
    line-height: 1.3;
    white-space: nowrap;
  }
  .card--front .brand-name {
    left: 346px; top: 58px; width: 210px;
    font-size: 19px; letter-spacing: 2px; color: var(--ink);
  }
  .card--back .brand-name {
    left: 0; top: 108px; width: 100%;
    font-size: 32px; letter-spacing: 4px; color: var(--white);
  }

  .person { position: absolute; left: 31px; top: 180px; }
  .person__name { font-size: 21px; font-weight: 700; letter-spacing: -0.3px; color: var(--ink); }
  .person__title { font-size: 15px; color: var(--ink-muted); margin-top: 1px; }

  .divider {
    position: absolute; left: 31px; top: 230px; width: 537px; height: 1px;
    background: var(--rule);
  }
  .divider__accent {
    position: absolute; left: 0; top: -1px; width: 117px; height: 4px;
    background: var(--ink);
  }

  .contact-list {
    position: absolute; left: 31px; top: 246px;
    list-style: none; font-size: 13px; letter-spacing: -0.1px; color: var(--ink-soft);
    white-space: nowrap;
  }
  .contact-list li { display: flex; align-items: center; height: 19px; }
  .contact-list svg { width: 12px; height: 12px; margin-right: 9px; fill: var(--ink); flex: none; }

  .address {
    position: absolute; right: 4px; top: 246px;
    font-style: normal; text-align: right; font-size: 13px; letter-spacing: -0.1px;
    line-height: 19px; color: var(--ink-soft); white-space: nowrap;
  }

  .website {
    position: absolute; left: 0; top: 292px; width: 100%;
    text-align: center; font-size: 14px; letter-spacing: 2.4px; color: var(--white);
  }
</style>
</head>
<body>
  <section class="card card--front" aria-label="Front of card">
    <p class="brand-name">Brightline<br>Tattoo Removal</p>

    <div class="person">
      <h1 class="person__name">MELISSA THORNBURY</h1>
      <p class="person__title">Chief Executive Offer</p>
    </div>

    <div class="divider"><span class="divider__accent"></span></div>

    <ul class="contact-list">
      <li>
        <svg viewBox="0 0 16 16" aria-hidden="true"><path d="M3.6 1.2l2.3 2.6-1.3 2c.9 2 2.5 3.6 4.6 4.6l2-1.3 2.6 2.3-1.2 2.4C6.8 13.5 2.5 9.2 1.2 3.4z"/></svg>
        919.362.4178
      </li>
      <li>
        <svg viewBox="0 0 16 16" aria-hidden="true"><path d="M4.5 0h7a1 1 0 0 1 1 1v14a1 1 0 0 1-1 1h-7a1 1 0 0 1-1-1V1a1 1 0 0 1 1-1zm.5 2v10.5h6V2zm3 11.2a.9.9 0 1 0 0 1.8.9.9 0 0 0 0-1.8z"/></svg>
        919.537.2846
      </li>
      <li>
        <svg viewBox="0 0 16 16" aria-hidden="true"><path d="M4 1h8v4H4zM1 6h14v6h-3v3H4v-3H1zm4 4v4h6v-4z"/></svg>
        919.685.3907
      </li>
      <li>
        <svg viewBox="0 0 16 16" aria-hidden="true"><path d="M1 3h14v1.2L8 9 1 4.2zm0 2.6l7 4.8 7-4.8V13H1z"/></svg>
        mthornbury@brightlinetattooremoval.example
      </li>
    </ul>

    <address class="address">
      4615 Oakmere Pkwy<br>
      Suite 210<br>
      Raleigh, NC 27654<br>
      www.brightlinetattooremoval.example
    </address>
  </section>

  <section class="card card--back" aria-label="Back of card">
    <p class="brand-name">Brightline<br>Tattoo Removal</p>
    <p class="website">www.brightlinetattooremoval.example</p>
  </section>
</body>
</html>
```